Corporate Business Card

Very professional, Modern, Not to busy, include phone address email, website
(253) 617-4930, 18761 52nd Avenue S, Kent, WA 98047, martin@plumlinegroup.com, varkoworks.com

Target Market(s)

Manufacturing

Industry/Entity Type

Aero, machining, manufacturing, Off road racing

Contact Information for Business Card

Phone, address email, website

```html
<!DOCTYPE html>
<html lang="en">
<head>
<meta charset="utf-8">
<title>Varko Works – Business Card</title>
<link href="https://fonts.googleapis.com/css2?family=Montserrat:wght@500;600;800&display=swap" rel="stylesheet">
<style>
  :root {
    --navy: #1b3a78;
    --navy-deep: #16306a;
    --red: #d7282f;
    --silver: #c9cbce;
    --ink: #1c1c1c;
    --paper: #ffffff;
    --stage: #e9eaec;
  }
  * { margin: 0; padding: 0; box-sizing: border-box; }
  html, body {
    width: 1200px; height: 1015px; overflow: hidden;
    background: var(--stage);
    font-family: "Montserrat", sans-serif;
  }
  .sheet {
    width: 1200px; height: 1015px;
    display: flex; flex-direction: column; align-items: center; justify-content: center;
    gap: 60px;
  }
  .card {
    position: relative;
    width: 600px; height: 343px;
    overflow: hidden;
    box-shadow: 0 6px 18px rgba(0,0,0,.18);
  }
  .card--front { background: var(--navy); }
  .card--back { background: var(--paper); }

  .brand {
    position: absolute;
    display: flex; flex-direction: column; align-items: flex-end;
  }
  .brand__name {
    font-weight: 800;
    letter-spacing: 1px;
    line-height: 1;
    text-transform: uppercase;
  }
  .brand__rule { height: 2px; margin-top: 12px; }

  .card--front .brand { left: 110px; top: 118px; }
  .card--front .brand__name { font-size: 66px; color: var(--silver); }
  .card--front .brand__rule { width: 300px; background: var(--silver); align-self: flex-start; }

  .card--back .brand { right: 40px; top: 40px; }
  .card--back .brand__row { display: flex; align-items: center; gap: 10px; }
  .card--back .brand__mark { width: 14px; height: 14px; background: var(--red); }
  .card--back .brand__name { font-size: 40px; color: var(--navy); }
  .card--back .brand__rule { width: 200px; background: var(--navy); align-self: flex-start; margin-left: 24px; }

  .address {
    position: absolute; left: 42px; top: 130px;
    font-size: 15px; font-weight: 500; color: var(--ink); line-height: 1.45;
  }
  .contacts {
    position: absolute; left: 42px; top: 192px;
    list-style: none;
    font-size: 14px; font-weight: 500; color: var(--ink);
  }
  .contacts li { display: flex; align-items: center; gap: 10px; height: 23px; }
  .contacts svg { width: 15px; height: 15px; flex: none; }
  .wave { position: absolute; left: 0; top: 0; width: 600px; height: 343px; }
</style>
</head>
<body>
<main class="sheet">
  <section class="card card--front" aria-label="Card front">
    <div class="brand">
      <span class="brand__name">Varko Works</span>
      <span class="brand__rule"></span>
    </div>
  </section>

  <section class="card card--back" aria-label="Card back">
    <svg class="wave" viewBox="0 0 600 343" aria-hidden="true">
      <path d="M0,292 C160,306 300,290 420,232 C500,194 560,184 600,180 L600,343 L0,343 Z" fill="var(--navy)"/>
      <path d="M105,286 C250,282 350,246 440,202 C505,170 555,160 585,157" fill="none" stroke="var(--red)" stroke-width="4" stroke-linecap="round"/>
    </svg>

    <div class="brand">
      <div class="brand__row">
        <span class="brand__mark"></span>
        <span class="brand__name">Varko Works</span>
      </div>
      <span class="brand__rule"></span>
    </div>

    <p class="address">18761 52nd Avenue S<br>Kent, WA 98047</p>

    <ul class="contacts">
      <li>
        <svg viewBox="0 0 16 16"><path fill="var(--red)" d="M3.5 1.5l2.3 2.6-1.3 1.9c.9 2 2.6 3.7 4.6 4.6l1.9-1.3 2.6 2.3-1.6 2.3C6.9 13.6 2.4 9.1 1.2 3.1z"/></svg>
        (253) 617-4930
      </li>
      <li>
        <svg viewBox="0 0 16 16"><rect x="1" y="3" width="14" height="10" fill="var(--red)"/><path d="M1.5 3.5 8 9l6.5-5.5" fill="none" stroke="#fff" stroke-width="1.2"/></svg>
        martin@plumlinegroup.com
      </li>
      <li>
        <svg viewBox="0 0 16 16"><circle cx="8" cy="8" r="7" fill="var(--red)"/><path d="M1 8h14M8 1c-3 3-3 11 0 14M8 1c3 3 3 11 0 14" fill="none" stroke="#fff" stroke-width="1"/></svg>
        www.varkoworks.com
      </li>
    </ul>
  </section>
</main>
</body>
</html>
```